Social Media Graphics - Oakline Push REVISED

Create 6-7 individual social media graphics (square size) to encourage folks to join our online course called:

The Harvest Ledger Circle
How to Launch a Multi-Million Business From Scratch
Sign Up Today!

IMPORTANT: Make the largest and most prominent text on the graphic be: How to Launch a Multi-Million Business From Scratch

For the color scheme of the graphics, let's try a blue color palette; make sure the graphics appeal to both men and women

Make sure each graphic contains 1 of the 3 pics attached (crop pic as needed); and make sure one of the graphics is all TEXT only.

Target Market(s)

men and women looking to start a business

Industry/Entity Type

Entrepreneurship

Colors
0054AA
0677BA
7BADD7
CADEEF
E8F1F8

Requirements
Must have
• All the text and use the 3 pics provided; one graphic can be all text; Simple, modern design that's easy to read

```html
<!DOCTYPE html>
<html lang="en">
<head>
<meta charset="utf-8">
<title>The Harvest Ledger Circle – Social Graphics</title>
<link rel="stylesheet" href="https://fonts.googleapis.com/css2?family=Bebas+Neue&display=swap">
<style>
  :root {
    --blue-deep: #0054AA;
    --blue-mid: #0677BA;
    --blue-soft: #7BADD7;
    --blue-pale: #CADEEF;
    --blue-mist: #E8F1F8;
    --white: #ffffff;
    --page: #ffffff;
  }
  * { box-sizing: border-box; margin: 0; padding: 0; }
  html, body { width: 1200px; height: 902px; overflow: hidden; background: var(--page); }
  body { position: relative; font-family: "Bebas Neue", "Oswald", sans-serif; color: var(--white); }

  .tile {
    position: absolute; width: 310px; height: 310px; overflow: hidden;
    background: linear-gradient(135deg, var(--blue-deep) 0%, var(--blue-mid) 55%, var(--blue-deep) 100%);
  }
  .tile--1 { left: 118px; top: 143px; }
  .tile--2 { left: 461px; top: 143px; }
  .tile--3 { left: 803px; top: 143px; }
  .tile--4 { left: 118px; top: 483px; }
  .tile--5 { left: 461px; top: 483px; }
  .tile--6 { left: 803px; top: 483px; }

  .course-name {
    position: absolute; left: 0; right: 0; font-style: italic; font-size: 27px;
    letter-spacing: -0.2px; line-height: 1; text-align: center;
    text-shadow: 1px 2px 3px rgba(0, 30, 80, 0.55); white-space: nowrap;
  }
  .headline {
    position: absolute; left: 0; right: 0; text-align: center;
    font-size: 34px; line-height: 39.5px; white-space: nowrap;
  }

  .photo { position: absolute; }
  .photo--duo { background: radial-gradient(ellipse at 50% 40%, #3a3f4a 0%, #1d2a4a 45%, rgba(10, 40, 100, 0) 75%); }
  .photo--stage { background: linear-gradient(180deg, #6f8fc0 0%, #3a5688 55%, #2b3e66 100%); }
  .photo--red { background: radial-gradient(ellipse at 50% 45%, #c94a5a 0%, #3b2e35 50%, rgba(10, 40, 100, 0) 78%); }

  .badge { position: absolute; width: 65px; height: 62px; }
  .badge svg { position: absolute; inset: 0; width: 100%; height: 100%; overflow: visible; }
  .badge-text {
    position: absolute; left: 0; right: 0; top: 6px; text-align: center;
    font-size: 21px; line-height: 19px; color: var(--blue-mid);
    -webkit-text-stroke: 1px var(--white);
    text-shadow: 0 0 4px rgba(202, 222, 239, 0.8);
  }
  .badge--lg { width: 90px; height: 82px; }
  .badge--lg .badge-text { font-size: 29px; line-height: 26px; top: 8px; }

  /* tile 1: text only */
  .tile--1 .course-name { text-align: left; left: 15px; top: 17px; font-size: 28px; }
  .tile--1 .headline { text-align: left; left: 15px; top: 64px; font-size: 47px; line-height: 50px; }

  /* tile 3 bands */
  .band-title { position: absolute; left: 0; right: 0; top: 128px; height: 48px; background: var(--blue-deep); border-top: 1px solid var(--blue-soft); border-bottom: 2px solid var(--blue-soft); }
  .band-lower { position: absolute; left: 0; right: 0; top: 176px; bottom: 0; background: linear-gradient(180deg, var(--blue-mid), #0a6db3); }
  .top-glow { position: absolute; left: 0; right: 0; top: 0; height: 128px; background: radial-gradient(ellipse at 40% 20%, var(--blue-soft) 0%, var(--blue-mid) 45%, var(--blue-deep) 90%); }

  .bokeh { position: absolute; border-radius: 50%; background: rgba(123, 173, 215, 0.35); }
</style>
</head>
<body>

<!-- Tile 1 -->
<section class="tile tile--1">
  <p class="course-name">The Harvest Ledger Circle</p>
  <h2 class="headline">How to launch<br>a multi-million<br>business from<br>scratch</h2>
  <div class="badge badge--lg" style="left:190px; top:222px;">
    <svg viewBox="0 0 90 82"><path d="M2 2 H88 V64 H48 L44 78 L38 64 H2 Z" fill="none" stroke="#fff" stroke-width="1.3"/></svg>
    <p class="badge-text">Sign up<br>today!</p>
  </div>
</section>

<!-- Tile 2 -->
<section class="tile tile--2" style="background: var(--blue-deep);">
  <svg style="position:absolute;inset:0" width="310" height="310" viewBox="0 0 310 310">
    <path d="M0 0 H310 L305 5 L292 30 L280 55 L268 80 L250 100 L228 120 L200 150 L180 175 L155 200 L120 230 L90 250 L60 265 L30 280 L15 300 L0 310 Z" fill="var(--blue-mid)"/>
    <path d="M310 0 L292 30 L268 80 L228 120 L180 175 L120 230 L60 265 L15 300 L0 310" fill="none" stroke="var(--blue-pale)" stroke-width="1.2" opacity="0.8"/>
  </svg>
  <p class="course-name" style="top:17px;">The Harvest Ledger Circle</p>
  <div class="photo photo--duo" role="img" aria-label="Photo of the two course hosts, arms crossed, smiling" style="left:128px; top:55px; width:157px; height:128px;"></div>
  <div class="badge badge--lg" style="left:22px; top:73px;">
    <svg viewBox="0 0 90 82"><path d="M2 2 H88 V64 H48 L44 78 L38 64 H2 Z" fill="none" stroke="#fff" stroke-width="1.3"/></svg>
    <p class="badge-text">Sign up<br>today!</p>
  </div>
  <h2 class="headline" style="top:176px;">How to launch a<br>multi-million business<br>from scratch</h2>
</section>

<!-- Tile 3 -->
<section class="tile tile--3">
  <div class="top-glow"></div>
  <div class="photo photo--stage" role="img" aria-label="Photo of the two hosts speaking on stage with a microphone" style="left:16px; top:20px; width:174px; height:108px;"></div>
  <div class="badge" style="left:209px; top:38px;">
    <svg viewBox="0 0 65 62"><path d="M1 1 H64 V48 H36 L32 60 L27 48 H1 Z" fill="none" stroke="#fff" stroke-width="1.2"/></svg>
    <p class="badge-text">Sign up<br>today!</p>
  </div>
  <div class="band-title"></div>
  <p class="course-name" style="top:139px; font-size:30px;">The Harvest Ledger Circle</p>
  <div class="band-lower"></div>
  <h2 class="headline" style="top:185px;">How to launch a<br>multi-million business<br>from scratch</h2>
</section>

<!-- Tile 4 -->
<section class="tile tile--4" style="background: var(--blue-deep);">
  <svg style="position:absolute;inset:0" width="310" height="310" viewBox="0 0 310 310">
    <path d="M0 310 C10 210 80 146 155 146 C230 146 300 210 310 310 Z" fill="var(--blue-mid)" stroke="var(--blue-pale)" stroke-width="1.2"/>
  </svg>
  <p class="course-name" style="top:18px;">The Harvest Ledger Circle</p>
  <div class="photo photo--red" role="img" aria-label="Photo of the two course hosts, one in a red dress, arms crossed" style="left:74px; top:62px; width:125px; height:125px;"></div>
  <div class="badge" style="left:221px; top:74px;">
    <svg viewBox="0 0 65 62"><path d="M1 1 H64 V48 H36 L32 60 L27 48 H1 Z" fill="none" stroke="#fff" stroke-width="1.2"/></svg>
    <p class="badge-text">Sign up<br>today!</p>
  </div>
  <h2 class="headline" style="top:188px;">How to launch a<br>multi-million business<br>from scratch</h2>
</section>

<!-- Tile 5 -->
<section class="tile tile--5" style="background: var(--blue-deep);">
  <svg style="position:absolute;inset:0" width="310" height="310" viewBox="0 0 310 310">
    <path d="M0 0 H22 L0 28 Z" fill="var(--blue-mid)"/>
    <path d="M22 0 H200 L250 40 L310 80 V200 L250 250 L155 190 L60 260 L0 200 V115 Z" fill="var(--blue-mid)"/>
    <path d="M200 0 H310 V80 Z" fill="var(--blue-deep)"/>
    <path d="M0 200 L60 260 M250 250 L310 200" stroke="var(--blue-pale)" stroke-width="1" opacity="0.7"/>
  </svg>
  <p class="course-name" style="top:16px;">The Harvest Ledger Circle</p>
  <h2 class="headline" style="top:58px;">How to launch a<br>multi-million business<br>from scratch</h2>
  <div class="photo photo--duo" role="img" aria-label="Photo of the two course hosts standing together, smiling" style="left:52px; top:181px; width:166px; height:129px;"></div>
  <div class="badge" style="left:218px; top:195px;">
    <svg viewBox="0 0 65 62"><path d="M1 1 H64 V48 H36 L32 60 L27 48 H1 Z" fill="none" stroke="#fff" stroke-width="1.2"/></svg>
    <p class="badge-text">Sign up<br>today!</p>
  </div>
</section>

<!-- Tile 6 -->
<section class="tile tile--6" style="background: radial-gradient(ellipse at 40% 45%, var(--blue-mid) 0%, var(--blue-deep) 80%);">
  <span class="bokeh" style="left:-6px; top:-4px; width:26px; height:26px;"></span>
  <span class="bokeh" style="left:10px; top:54px; width:22px; height:22px;"></span>
  <span class="bokeh" style="left:285px; top:76px; width:22px; height:22px;"></span>
  <span class="bokeh" style="left:14px; top:160px; width:22px; height:22px;"></span>
  <span class="bokeh" style="left:150px; top:205px; width:22px; height:22px;"></span>
  <span class="bokeh" style="left:12px; top:255px; width:22px; height:22px;"></span>
  <span class="bokeh" style="left:68px; top:287px; width:22px; height:22px;"></span>
  <span class="bokeh" style="left:120px; top:250px; width:20px; height:20px;"></span>
  <span class="bokeh" style="left:290px; top:20px; width:20px; height:20px;"></span>
  <p class="course-name" style="top:16px;">The Harvest Ledger Circle</p>
  <h2 class="headline" style="top:58px;">How to launch a<br>multi-million business<br>from scratch</h2>
  <div class="badge" style="left:45px; top:205px;">
    <svg viewBox="0 0 65 62"><path d="M1 1 H64 V48 H36 L32 60 L27 48 H1 Z" fill="none" stroke="#fff" stroke-width="1.2"/></svg>
    <p class="badge-text">Sign up<br>today!</p>
  </div>
  <div class="photo photo--stage" role="img" aria-label="Photo of the two hosts speaking on stage with a microphone" style="left:144px; top:184px; width:166px; height:126px;"></div>
</section>

</body>
</html>
```